Dunmore Roofing

Want a professional looking business card

Industry/Entity Type

Business

Contact Information for Business Card

Paul Dunmore ( Owner) paul@dunmoreroofing-example.com, www.dunmoreroofing-example.com, Adress: 4172 Township road 43 Plantagenet,ON K9X4T2

```html
<!DOCTYPE html>
<html lang="en">
<head>
<meta charset="utf-8">
<title>Dunmore Roofing – Business Card</title>
<link rel="stylesheet" href="https://fonts.googleapis.com/css2?family=Roboto:wght@400;700&family=Roboto+Condensed:wght@400;700&display=swap">
<style>
  :root {
    --backdrop: #2b2b2b;
    --card: #f4f4f4;
    --brand-blue: #1a4687;
    --text-grey: #555555;
    --soft-grey: #6e6e6e;
  }
  * { box-sizing: border-box; margin: 0; padding: 0; }
  html, body { width: 1200px; height: 960px; overflow: hidden; }
  body {
    background: var(--backdrop);
    position: relative;
    font-family: "Roboto", Arial, sans-serif;
  }
  .card {
    position: absolute;
    left: 320px;
    width: 600px;
    background: var(--card);
    border-radius: 18px;
    overflow: hidden;
  }
  .card-front { top: 95px; height: 355px; }
  .card-back { top: 493px; height: 342px; }

  .front-name {
    position: absolute;
    top: 148px;
    width: 100%;
    text-align: center;
    color: var(--brand-blue);
    font-weight: 700;
    font-size: 46px;
    line-height: 1;
    letter-spacing: 2px;
    text-transform: uppercase;
  }
  .front-web {
    position: absolute;
    top: 298px;
    width: 100%;
    text-align: center;
    color: var(--text-grey);
    font-size: 14px;
    letter-spacing: 4px;
  }

  .back-name {
    position: absolute;
    right: 40px;
    top: 42px;
    text-align: right;
    color: var(--brand-blue);
    font-weight: 700;
    font-size: 44px;
    line-height: 1.1;
    text-transform: uppercase;
  }
  .side-tab {
    position: absolute;
    left: -22px;
    top: 156px;
    width: 44px;
    height: 44px;
    border-radius: 50%;
    background: var(--brand-blue);
  }
  .person {
    position: absolute;
    left: 35px;
    top: 157px;
  }
  .person-name {
    font-family: "Roboto Condensed", Arial, sans-serif;
    color: var(--brand-blue);
    font-size: 22px;
    text-transform: uppercase;
    line-height: 1.1;
  }
  .person-role {
    font-family: "Roboto Condensed", Arial, sans-serif;
    color: var(--soft-grey);
    font-size: 15px;
    text-transform: uppercase;
    margin-top: 3px;
  }
  .address {
    margin-top: 10px;
    color: var(--text-grey);
    font-size: 14px;
    line-height: 18px;
  }
  .contacts { margin-top: 8px; list-style: none; }
  .contacts li {
    display: flex;
    align-items: center;
    gap: 8px;
    color: var(--text-grey);
    font-size: 14px;
    line-height: 19px;
  }
  .contacts svg { width: 14px; height: 14px; fill: var(--brand-blue); flex: none; }
</style>
</head>
<body>
  <section class="card card-front">
    <div class="front-name">Dunmore Roofing</div>
    <div class="front-web">www.dunmoreroofing-example.com</div>
  </section>

  <section class="card card-back">
    <div class="back-name">Dunmore<br>Roofing</div>
    <div class="side-tab"></div>
    <div class="person">
      <div class="person-name">Paul Dunmore</div>
      <div class="person-role">Owner</div>
      <p class="address">4172 Township road 43<br>Ashbury Falls, ON K9X4T2</p>
      <ul class="contacts">
        <li>
          <svg viewBox="0 0 24 24" aria-hidden="true"><path d="M6.6 10.8a15 15 0 0 0 6.6 6.6l2.2-2.2a1 1 0 0 1 1-.25 11.4 11.4 0 0 0 3.6.57 1 1 0 0 1 1 1V20a1 1 0 0 1-1 1A17 17 0 0 1 3 4a1 1 0 0 1 1-1h3.5a1 1 0 0 1 1 1c0 1.25.2 2.45.57 3.57a1 1 0 0 1-.25 1z"/></svg>
          613 555 0148
        </li>
        <li>
          <svg viewBox="0 0 24 24" aria-hidden="true"><path d="M2 5h20v14H2z"/><path d="M3 6l9 7 9-7" fill="none" stroke="#f4f4f4" stroke-width="2"/></svg>
          paul@dunmoreroofing-example.com
        </li>
        <li>
          <svg viewBox="0 0 24 24" aria-hidden="true"><circle cx="12" cy="12" r="10"/><path d="M7 8c2 0 3 1 3 3s-2 2-2 4 2 3 2 5M14 4c0 2 2 3 4 3M15 14c1 0 2 1 2 3" fill="none" stroke="#f4f4f4" stroke-width="1.6"/></svg>
          www.dunmoreroofing-example.com
        </li>
      </ul>
    </div>
  </section>
</body>
</html>
```